Valdane Companies Business Card Design

We need a new business card for our Private Equity Real Estate Development firm, “Valdane” and our EB-5 regional center “Thornmere Regional Center” on one card. We prefer a design that is simple, elegant, and represents the luxury products we design and build as well as the financial security and stability our successful history has produced. We are an industry leader in our field and 3rd generation family business that has evolved into an institutional quality investment platform. Considered design size is standard business card dimensions (3.5 x 2 inches with an additional 1/8 inch space for design elements or backgrounds that extend beyond the finished size of your piece.

Target Market(s)

• High net worth individuals
• Highly skilled technical workers and physicians in the US seeking investment-based immigration opportunities
• Sophisticated private equity investors
• Intermediary partners include domestic attorneys and investment brokers, as well as international agent networks
• US real estate developers

Industry/Entity Type

Finance

Contact Information for Business Card

(Providing placeholder info for personal information, please design for longer character spaces, longer names and addresses etc..)
• Logo for Valdane
• Logo for Thornmere Regional Center
• Full name: Marcus Valdane
• Job title: CEO
• Email address: mvaldane@valdanecompanies.com
• Cell phone number: +1.555.314.2287
• Office number +1.555.628.4410
• Office address: Larkfield Court 5, 4817 Vista Orilla, Alder Bay, OR.
• Website: www.valdanecompanies.com

Font styles to use
Serif
Sans Serif

Colors
ec1f27
ffffff
000000

Requirements
Must have
• • Logo for Valdane
• • Logo for Thornmere Regional Center
• - Use rounded corners
• (See .ai file included for logos)
Nice to have
• • Simple, elegant design
• • Aesthetically compatible with our website design (www.valdanecompanies.com)
• • Color palette including but not limited to white, black, and red (as per logos)
Should not have
• - Not too much red color
• - Do not stack both logos on top of each other

```html
<!DOCTYPE html>
<html lang="en">
<head>
<meta charset="utf-8">
<title>Valdane Companies Business Card</title>
<link href="https://fonts.googleapis.com/css2?family=Cormorant+Garamond:wght@400;600&family=Arimo:wght@400;700&display=swap" rel="stylesheet">
<style>
  :root {
    --bg: #e6e6e4;
    --card-dark-1: #3a3a3b;
    --card-dark-2: #1c1c1d;
    --map-tone: #4a4a4c;
    --silver: #9c9c9e;
    --paper: #ffffff;
    --ink: #2b2b2b;
    --ink-soft: #555555;
    --rule: #3a3a3a;
    --brand-red: #b0183a;
  }
  * { box-sizing: border-box; margin: 0; padding: 0; }
  html, body { width: 1200px; height: 900px; overflow: hidden; }
  body { background: var(--bg); position: relative; font-family: "Arimo", sans-serif; }

  .card {
    position: absolute;
    left: 285px;
    width: 630px;
    height: 360px;
    border-radius: 22px;
    overflow: hidden;
    box-shadow: 0 10px 30px rgba(0,0,0,0.18);
  }

  /* Front */
  .card-front {
    top: 50px;
    background: linear-gradient(160deg, var(--card-dark-1), var(--card-dark-2));
  }
  .world-map-area {
    position: absolute;
    left: 40px; top: 40px; right: 40px; bottom: 40px;
    border-radius: 12px;
    background: radial-gradient(ellipse at 50% 50%, var(--map-tone) 0%, rgba(74,74,76,0.25) 60%, rgba(74,74,76,0) 100%);
    opacity: 0.55;
  }
  .front-brand {
    position: absolute;
    left: 0; right: 0; top: 150px;
    display: flex; align-items: center; justify-content: center; gap: 18px;
  }
  .brand-square {
    width: 40px; height: 40px;
    border: 2px solid var(--silver);
  }
  .front-brand-name {
    font-family: "Cormorant Garamond", serif;
    font-weight: 600;
    font-size: 46px;
    letter-spacing: 4px;
    color: var(--silver);
    text-transform: uppercase;
  }

  /* Back */
  .card-back {
    top: 490px;
    background: var(--paper);
  }
  .back-brand {
    position: absolute;
    right: 40px; top: 38px;
    display: flex; flex-direction: column; align-items: flex-end; gap: 10px;
  }
  .back-brand-square {
    width: 34px; height: 34px;
    background: var(--brand-red);
  }
  .back-brand-name {
    font-family: "Cormorant Garamond", serif;
    font-weight: 600;
    font-size: 22px;
    letter-spacing: 2px;
    color: var(--brand-red);
    text-transform: uppercase;
    text-align: right;
    line-height: 1.1;
  }
  .person-name {
    position: absolute;
    left: 40px; top: 172px;
    font-family: "Cormorant Garamond", serif;
    font-weight: 400;
    font-size: 32px;
    letter-spacing: 2px;
    color: var(--ink);
    text-transform: uppercase;
  }
  .person-title {
    position: absolute;
    left: 48px; top: 214px;
    font-family: "Cormorant Garamond", serif;
    font-size: 22px;
    color: var(--ink);
    text-transform: uppercase;
  }
  .divider {
    position: absolute;
    left: 112px; right: 40px; top: 226px;
    height: 1px;
    background: var(--rule);
  }
  .address {
    position: absolute;
    right: 40px; top: 238px;
    font-size: 13px;
    line-height: 1.45;
    color: var(--ink-soft);
    text-align: right;
  }
  .contact-list {
    position: absolute;
    left: 48px; top: 256px;
    list-style: none;
    font-size: 14px;
    line-height: 1.55;
    color: var(--ink-soft);
  }
  .contact-label { font-weight: 700; color: var(--ink); margin-right: 4px; }
  .contact-web { font-weight: 700; color: var(--ink); }
</style>
</head>
<body>
  <section class="card card-front" aria-label="Card front">
    <div class="world-map-area" role="img" aria-label="Faint dotted world map in dark grey tones"></div>
    <div class="front-brand">
      <span class="brand-square"></span>
      <span class="front-brand-name">Valdane Capital</span>
    </div>
  </section>

  <section class="card card-back" aria-label="Card back">
    <div class="back-brand">
      <span class="back-brand-square"></span>
      <span class="back-brand-name">Thornmere<br>Regional Center</span>
    </div>

    <h1 class="person-name">Marcus Valdane</h1>
    <p class="person-title">CEO</p>
    <div class="divider"></div>

    <p class="address">Larkfield Court 5, 4817 Vista Orilla,<br>Alder Bay, OR.</p>

    <ul class="contact-list">
      <li><span class="contact-label">C:</span>+1.555.314.2287</li>
      <li><span class="contact-label">P:</span>+1.555.628.4410</li>
      <li><span class="contact-label">M:</span>mvaldane@valdanecompanies.com</li>
      <li><span class="contact-label">W:</span>www.<span class="contact-web">valdanecompanies</span>.com</li>
    </ul>
  </section>
</body>
</html>
```